Redesign of business card for Cedar Ridge Mechanical

We are looking for a new design for our business cards for Cedar Ridge Mechanical. We are a plumbing & HVAC construction company, operating on the West Coast of Canada and USA. Logo attached.
Industry/Entity Type
Construction - Plumbing & HVAC
Contact Information for Business Card
Name, address, phone numbers, email, website address
Look and feel
Each slider illustrates characteristics of the customer's brand and the style your logo design should communicate.

```html
<!DOCTYPE html>
<html lang="en">
<head>
<meta charset="utf-8">
<title>Cedar Ridge Mechanical – Business Card</title>
<link rel="stylesheet" href="https://fonts.googleapis.com/css2?family=Montserrat:wght@400;600;700&display=swap">
<style>
  :root {
    --backdrop: #c9c9c9;
    --card: #ffffff;
    --ink: #111111;
    --band: #000000;
    --swoosh: #8a8a8a;
    --reverse: #ffffff;
  }
  * { margin: 0; padding: 0; box-sizing: border-box; }
  html, body { width: 1200px; height: 896px; overflow: hidden; }
  body {
    background: var(--backdrop);
    font-family: "Montserrat", Arial, sans-serif;
    color: var(--ink);
    position: relative;
  }
  .card {
    position: absolute;
    left: 334px;
    width: 527px;
    height: 300px;
    background: var(--card);
    border-radius: 22px;
    overflow: hidden;
    box-shadow: 0 14px 24px rgba(0,0,0,0.18);
  }
  .card--front { top: 126px; }
  .card--back { top: 475px; }

  .brand {
    position: absolute;
    left: 0; right: 0;
    display: flex;
    align-items: center;
    justify-content: center;
    gap: 12px;
    font-weight: 700;
    text-transform: uppercase;
    color: var(--ink);
    letter-spacing: 1px;
  }
  .brand__mark { background: var(--ink); display: block; }
  .card--front .brand { top: 128px; font-size: 27px; }
  .card--front .brand__mark { width: 26px; height: 26px; }
  .card--back .brand { top: 70px; font-size: 20px; }
  .card--back .brand__mark { width: 20px; height: 20px; }

  .person {
    position: absolute;
    right: 291px;
    top: 176px;
    text-align: right;
  }
  .person__name { font-size: 20px; font-weight: 700; letter-spacing: 0.3px; line-height: 24px; }
  .person__role { font-size: 14px; font-weight: 400; line-height: 20px; margin-top: 2px; }

  .divider {
    position: absolute;
    left: 257px; top: 174px;
    width: 2px; height: 51px;
    background: var(--ink);
  }
  .contacts {
    position: absolute;
    left: 279px; top: 170px;
    list-style: none;
    font-size: 14px;
    line-height: 20px;
  }
  .contacts li { display: flex; align-items: center; gap: 4px; }
  .contacts svg { width: 12px; height: 12px; flex: none; }

  .footer-band { position: absolute; left: 0; top: 210px; width: 527px; height: 90px; }
  .address {
    position: absolute;
    left: 0; right: 0; top: 269px;
    text-align: center;
    color: var(--reverse);
    font-size: 13.5px;
  }
</style>
</head>
<body>

<section class="card card--front">
  <div class="brand"><span class="brand__mark"></span>Cedar Ridge Mechanical</div>
</section>

<section class="card card--back">
  <div class="brand"><span class="brand__mark"></span>Cedar Ridge Mechanical</div>

  <div class="person">
    <p class="person__name">JAMES BROWN</p>
    <p class="person__role">Managing Director</p>
  </div>

  <div class="divider"></div>

  <ul class="contacts">
    <li>
      <svg viewBox="0 0 24 24" aria-hidden="true"><path fill="var(--ink)" d="M6.6 10.8a15 15 0 0 0 6.6 6.6l2.2-2.2c.3-.3.7-.4 1-.2 1.1.4 2.3.6 3.6.6.6 0 1 .4 1 1V20c0 .6-.4 1-1 1A17 17 0 0 1 3 4c0-.6.4-1 1-1h3.5c.6 0 1 .4 1 1 0 1.3.2 2.5.6 3.6.1.3 0 .7-.2 1z"/></svg>
      123 456 789
    </li>
    <li>
      <svg viewBox="0 0 24 24" aria-hidden="true"><rect x="2" y="5" width="20" height="14" rx="2" fill="none" stroke="var(--ink)" stroke-width="2.4"/><path d="M3 6l9 7 9-7" fill="none" stroke="var(--ink)" stroke-width="2.4"/></svg>
      info@yourgmail.com
    </li>
    <li>
      <svg viewBox="0 0 24 24" aria-hidden="true"><circle cx="12" cy="12" r="10" fill="var(--ink)"/><path d="M2 12h20M12 2c3 3 3 17 0 20M12 2c-3 3-3 17 0 20" fill="none" stroke="#fff" stroke-width="1.4"/></svg>
      www.yourwebsite.com
    </li>
  </ul>

  <svg class="footer-band" viewBox="0 0 527 90" aria-hidden="true">
    <path d="M0 9 Q263 80 527 9 V90 H0 Z" fill="var(--band)"/>
    <path d="M20 9 Q263 70 507 5 Q263 62 20 9 Z" fill="var(--swoosh)"/>
  </svg>
  <p class="address">Your address, City State, Zip 1234</p>
</section>

</body>
</html>
```